Web Developer Needs a Business Card Design

I need a personal business card design that represents me as a web developer for potential employers. I would like the background to be a dark color on the front for contrast with my logo and name. The back will have all my information along with a smaller version of the logo. I want something with a modern look and feel, not too conservative. This will be used for potential employers and freelance work.

Industry/Entity Type

Business

Contact Information for Business Card

Front should have my logo and name. The back should have all my personal information which would include: name: Tom Varulek, phone: 570-614-3098, email: tomvarulek@quillbox.net, website url: www.tomvarulek.net, logo, web developer.

Font styles to use
Sans Serif

Requirements
Must have
• Must include my logo. The color palette base color will be the logo color.

```html
<!DOCTYPE html>
<html lang="en">
<head>
<meta charset="utf-8">
<title>Tom Varulek — Business Card</title>
<link rel="stylesheet" href="https://fonts.googleapis.com/css2?family=Open+Sans:wght@400;600;700&display=swap">
<style>
  :root {
    --teal: #4de2c3;
    --teal-deep: #3fc9ad;
    --white: #ffffff;
    --ink: #555a5c;
    --stage: #eceeee;
  }
  * { margin: 0; padding: 0; box-sizing: border-box; }
  html, body {
    width: 1200px; height: 900px; overflow: hidden;
    background: var(--stage);
    font-family: "Open Sans", Arial, sans-serif;
  }
  .card {
    position: absolute;
    width: 556px; height: 342px;
    overflow: hidden;
    box-shadow: 0 6px 18px rgba(0,0,0,.18);
  }
  /* Contact side */
  .card--contact { left: 237px; top: 62px; background: var(--white); }
  .side-band {
    position: absolute; left: 36px; top: 0;
    width: 92px; height: 100%;
    background: var(--teal);
  }
  .brand-badge {
    position: absolute; left: 36px; top: 51px;
    width: 94px; height: 94px;
    border: 5px solid var(--white); border-radius: 50%;
    display: flex; align-items: center; justify-content: center;
    color: var(--white); font-weight: 700; font-size: 15px;
  }
  .corner-ring { position: absolute; left: 0; top: 0; }
  .contact-block { position: absolute; left: 190px; top: 156px; color: var(--ink); }
  .contact-name { color: var(--teal-deep); font-size: 18px; font-weight: 600; line-height: 24px; }
  .contact-role { font-size: 15px; line-height: 22px; }
  .contact-list { list-style: none; margin-top: 15px; }
  .contact-list li {
    display: flex; align-items: center; gap: 8px;
    font-size: 15px; line-height: 20px;
  }
  .contact-list svg { width: 10px; height: 10px; flex: none; }
  /* Brand side */
  .card--brand { left: 458px; top: 518px; background: var(--teal); }
  .brand-seal {
    position: absolute; left: 179px; top: 45px;
    width: 200px; height: 200px;
    border: 4px solid var(--teal-deep); border-radius: 50%;
    display: flex; align-items: center; justify-content: center;
    color: var(--teal-deep); font-weight: 700; font-size: 30px;
  }
  .brand-name {
    position: absolute; left: 0; right: 0; top: 264px;
    text-align: center; color: var(--white);
    font-size: 26px; font-weight: 700;
  }
</style>
</head>
<body>
  <section class="card card--contact">
    <div class="side-band"></div>
    <div class="brand-badge">Varulek</div>
    <svg class="corner-ring" width="556" height="342" viewBox="0 0 556 342" aria-hidden="true">
      <circle cx="590" cy="125" r="140" fill="none" stroke="var(--teal)" stroke-width="16"/>
    </svg>
    <div class="contact-block">
      <p class="contact-name">Tom Varulek</p>
      <p class="contact-role">Front-End Developer</p>
      <ul class="contact-list">
        <li><svg viewBox="0 0 10 10"><path d="M2 0.5 L4 2.5 L3 4 Q4.5 6 6 7 L7.5 6 L9.5 8 L8 9.5 Q3 9 0.5 2 Z" fill="var(--teal-deep)"/></svg>570-614-3098</li>
        <li><svg viewBox="0 0 10 10"><rect x="0.5" y="2" width="9" height="6.5" fill="var(--teal-deep)"/><path d="M0.5 2 L5 5.5 L9.5 2" fill="none" stroke="#fff" stroke-width="0.9"/></svg>tomvarulek@quillbox.net</li>
        <li><svg viewBox="0 0 10 10"><circle cx="5" cy="5" r="4.3" fill="none" stroke="var(--teal-deep)" stroke-width="1.1"/><path d="M0.7 5 H9.3 M5 0.7 V9.3" stroke="var(--teal-deep)" stroke-width="0.9"/></svg>www.tomvarulek.net</li>
      </ul>
    </div>
  </section>

  <section class="card card--brand">
    <div class="brand-seal">Varulek</div>
    <p class="brand-name">Tom Varulek</p>
  </section>
</body>
</html>
```